Velvet Lantern rebranding my business with a new business card

I have my new logo and now I need a refresher on my business cards. I really want something fun and fresh. I like black background or anything to make the color pop.
Logo
Name: Velvet Lantern
Contact Info as stated below:
Mira Pellow
555-013-4762
Logo
Name: Velvet Lantern
Mira Pellow
555-013-4762
fb.me/VelvetLanternbyMira
Instagram: @VelvetLanternbyMira

Industry/Entity Type

Business

Contact Information for Business Card

double-sided. Logo on one side. Contact info on the other.

Requirements
Must have
• Logo
• Name: Velvet Lantern
• Contact Info as stated below:
• Mira Pellow
• 555-013-4762
• fb.me/VelvetLanternbyMira
• fb.me/VelvetLanternbyMira

```html
<!DOCTYPE html>
<html lang="en">
<head>
<meta charset="utf-8">
<title>Velvet Lantern – Business Card</title>
<link href="https://fonts.googleapis.com/css2?family=Roboto:wght@400;500&family=Roboto+Condensed:wght@700&display=swap" rel="stylesheet">
<style>
  :root {
    --backdrop: #e9e4de;
    --card-dark: #1b1c1e;
    --card-light: #f3f3f3;
    --band: #000000;
    --ink-light: #ffffff;
    --ink-dark: #2f2f2f;
    --brand-pink: #f0a6c6;
    --brand-faint: rgba(232, 170, 196, 0.22);
    --ring: #f2c6d8;
  }
  html, body {
    margin: 0;
    padding: 0;
    width: 1200px;
    height: 960px;
    overflow: hidden;
    background: var(--backdrop);
  }
  .canvas {
    position: relative;
    width: 1200px;
    height: 960px;
  }
  .card {
    position: absolute;
    border-radius: 18px;
    overflow: hidden;
    box-shadow: 0 6px 14px rgba(0, 0, 0, 0.25);
  }
  /* Front */
  .card-front {
    left: 320px;
    top: 102px;
    width: 610px;
    height: 352px;
    background: var(--card-dark);
  }
  .front-brand {
    position: absolute;
    left: 0;
    right: 0;
    top: 140px;
    margin: 0;
    text-align: center;
    font-family: "Roboto Condensed", sans-serif;
    font-weight: 700;
    font-size: 44px;
    line-height: 56px;
    color: var(--brand-pink);
  }
  .front-web {
    position: absolute;
    left: 0;
    right: 0;
    top: 296px;
    text-align: center;
    font-family: "Roboto", sans-serif;
    font-size: 14px;
    letter-spacing: 6px;
    color: var(--ink-light);
  }
  /* Back */
  .card-back {
    left: 320px;
    top: 492px;
    width: 600px;
    height: 343px;
    background: var(--card-light);
  }
  .back-watermark {
    position: absolute;
    left: 10px;
    top: 96px;
    width: 330px;
    text-align: center;
    font-family: "Roboto Condensed", sans-serif;
    font-weight: 700;
    font-size: 58px;
    line-height: 1;
    color: var(--brand-faint);
  }
  .name-band {
    position: absolute;
    left: 320px;
    top: 45px;
    width: 280px;
    height: 97px;
    background: var(--band);
  }
  .badge {
    position: absolute;
    left: 323px;
    top: 46px;
    width: 92px;
    height: 92px;
    border-radius: 50%;
    background: #ffffff;
    border: 2px solid var(--ring);
    box-sizing: border-box;
    display: flex;
    align-items: center;
    justify-content: center;
    text-align: center;
    font-family: "Roboto Condensed", sans-serif;
    font-weight: 700;
    font-size: 13px;
    line-height: 1.1;
    color: var(--brand-pink);
  }
  .holder-name {
    position: absolute;
    left: 450px;
    top: 78px;
    margin: 0;
    font-family: "Roboto Condensed", sans-serif;
    font-weight: 700;
    font-size: 21px;
    line-height: 28px;
    color: var(--ink-light);
    text-transform: uppercase;
  }
  .contact-list {
    position: absolute;
    left: 33px;
    top: 246px;
    margin: 0;
    padding: 0;
    list-style: none;
    font-family: "Roboto", sans-serif;
    font-size: 14px;
    color: var(--ink-dark);
  }
  .contact-list li {
    display: flex;
    align-items: center;
    height: 19px;
  }
  .contact-list svg {
    width: 12px;
    height: 12px;
    margin-right: 12px;
    fill: var(--ink-dark);
  }
</style>
</head>
<body>
<main class="canvas">
  <section class="card card-front" aria-label="Card front">
    <p class="front-brand">Velvet Lantern</p>
    <div class="front-web">www.velvetlantern.com</div>
  </section>

  <section class="card card-back" aria-label="Card back">
    <div class="back-watermark" aria-hidden="true">Velvet<br>Lantern</div>
    <div class="name-band"></div>
    <div class="badge">Velvet<br>Lantern</div>
    <h1 class="holder-name">Mira Pellow</h1>
    <ul class="contact-list">
      <li>
        <svg viewBox="0 0 24 24" aria-hidden="true"><path d="M6.6 10.8c1.4 2.8 3.8 5.1 6.6 6.6l2.2-2.2c.3-.3.7-.4 1-.2 1.1.4 2.3.6 3.6.6.6 0 1 .4 1 1V20c0 .6-.4 1-1 1C10.6 21 3 13.4 3 4c0-.6.4-1 1-1h3.5c.6 0 1 .4 1 1 0 1.3.2 2.5.6 3.6.1.3 0 .7-.2 1L6.6 10.8z"/></svg>
        555-013-4762
      </li>
      <li>
        <svg viewBox="0 0 24 24" aria-hidden="true"><path d="M12 2a10 10 0 1 0 0 20 10 10 0 0 0 0-20zm-1 17.9A8 8 0 0 1 4.1 11L9 16v1c0 1.1.9 2 2 2v.9zm6.9-2.5c-.3-.8-1-1.4-1.9-1.4h-1v-3c0-.6-.4-1-1-1H8v-2h2c.6 0 1-.4 1-1V7h2c1.1 0 2-.9 2-2v-.4a8 8 0 0 1 2.9 12.8z"/></svg>
        www.velvetlantern.com
      </li>
      <li>
        <svg viewBox="0 0 24 24" aria-hidden="true"><rect x="2" y="2" width="20" height="20" rx="2"/></svg>
        fb.me/VelvetLanternbyMira
      </li>
      <li>
        <svg viewBox="0 0 24 24" aria-hidden="true"><circle cx="12" cy="12" r="10"/></svg>
        @VelvetLanternbyMira
      </li>
    </ul>
  </section>
</main>
</body>
</html>
```